Tovel & Associates - London New Letting and Property Management Company *

Tovel & Associates LTD is a new company based in London, and works with brand new residential property in the city centre.

We are aiming to have 1000 new properties a year.

We are looking for something modern and minimalistic :
Logo ,Monogram, Paper Head and Business Card.

Target Market(s)

Internation landlords

Industry/Entity Type

Real Estate

Logo Text

Tovel & Associates

Colors

Designer to choose colors to be used in the design.

Requirements
Nice to have
• A particular monogram with "TA"
Should not have
• Little House over the logo

```html
<!DOCTYPE html>
<html lang="en">
<head>
<meta charset="utf-8">
<title>Tovel &amp; Associates – Business Card</title>
<link href="https://fonts.googleapis.com/css2?family=Work+Sans:wght@400;500;600&display=swap" rel="stylesheet">
<style>
  :root {
    --stage: #161616;
    --card: #252525;
    --card-edge: #1e1e1e;
    --accent: #29abe2;
    --accent-deep: #1f5580;
    --ink: #f2f2f2;
  }
  * { box-sizing: border-box; margin: 0; padding: 0; }
  html, body { width: 1200px; height: 900px; overflow: hidden; }
  body {
    background: var(--stage);
    font-family: "Work Sans", Arial, sans-serif;
    display: flex;
    flex-direction: column;
    align-items: center;
    justify-content: center;
    gap: 44px;
  }
  .card {
    position: relative;
    width: 700px;
    height: 380px;
    background: linear-gradient(135deg, var(--card) 0%, #2c2c2c 60%, var(--card-edge) 100%);
    border-bottom: 6px solid var(--accent);
    box-shadow: 0 18px 40px rgba(0,0,0,.55);
  }
  .brand {
    display: flex;
    align-items: center;
    gap: 14px;
    color: var(--accent);
    font-weight: 600;
    text-transform: uppercase;
    letter-spacing: 2px;
  }
  .brand-square {
    width: 22px; height: 22px;
    border: 4px solid var(--accent-deep);
    flex: none;
  }
  .card-front .brand {
    position: absolute;
    left: 50%; top: 50%;
    transform: translate(-50%, -50%);
    font-size: 24px;
  }
  .card-back { display: flex; align-items: center; }
  .card-back .brand {
    width: 300px;
    justify-content: center;
    font-size: 17px;
  }
  .divider {
    width: 2px; height: 190px;
    background: var(--accent);
  }
  .details { padding-left: 48px; color: var(--ink); }
  .person-name {
    color: var(--accent);
    font-size: 30px;
    font-weight: 500;
    letter-spacing: 2px;
    text-transform: uppercase;
    line-height: 1;
  }
  .person-role { font-size: 18px; margin: 6px 0 18px; }
  .address { font-size: 18px; line-height: 1.3; margin-bottom: 14px; }
  .contact-list { list-style: none; font-size: 18px; line-height: 1.55; }
  .contact-list li { display: flex; align-items: center; gap: 10px; }
  .contact-list svg { width: 12px; height: 12px; flex: none; }
</style>
</head>
<body>
  <section class="card card-front">
    <div class="brand"><span class="brand-square"></span>Tovel &amp; Associates</div>
  </section>

  <section class="card card-back">
    <div class="brand"><span class="brand-square"></span>Tovel &amp; Associates</div>
    <div class="divider"></div>
    <div class="details">
      <h1 class="person-name">Daniel Harrow</h1>
      <p class="person-role">Director</p>
      <p class="address">22 Wren Terrace<br>London EC2A 4BX</p>
      <ul class="contact-list">
        <li>
          <svg viewBox="0 0 12 12" aria-hidden="true"><path d="M2 1h3l1 3-1.5 1a7 7 0 0 0 2.5 2.5L8 6l3 1v3a1 1 0 0 1-1 1A9 9 0 0 1 1 2a1 1 0 0 1 1-1z" fill="var(--accent)"/></svg>
          +44 20 7946 0831
        </li>
        <li>
          <svg viewBox="0 0 12 12" aria-hidden="true"><rect x="1" y="2.5" width="10" height="7" fill="none" stroke="var(--accent)" stroke-width="1.2"/><path d="M1 3l5 3.5L11 3" fill="none" stroke="var(--accent)" stroke-width="1.2"/></svg>
          info@tovel&amp;associates.com
        </li>
        <li>
          <svg viewBox="0 0 12 12" aria-hidden="true"><circle cx="6" cy="6" r="5" fill="none" stroke="var(--accent)" stroke-width="1.1"/><ellipse cx="6" cy="6" rx="2.2" ry="5" fill="none" stroke="var(--accent)" stroke-width="1"/><path d="M1 6h10" stroke="var(--accent)" stroke-width="1"/></svg>
          www.tovel&amp;associates.com
        </li>
      </ul>
    </div>
  </section>
</body>
</html>
```